Automotive Business Card Design

I would just like a automotive themed card. nothing too extravagant, but catchy.

needs to say something about doing roadside assistance,mobile repairs, Diesel repairs, and Fleet maintenance

it can be single sided or double sided. no preference there.

Industry/Entity Type

Automotive

Contact Information for Business Card

Dean Marlowe
phone 534 861 2093
Name: Brightpath Automotive & Diesel Repair

```html
<!DOCTYPE html>
<html lang="en">
<head>
<meta charset="utf-8">
<title>Brightpath Automotive &amp; Diesel Repair — Business Card</title>
<link rel="stylesheet" href="https://fonts.googleapis.com/css2?family=Cinzel:wght@400&family=Open+Sans:wght@400&display=swap">
<style>
  :root {
    --backdrop: #2b2b2b;
    --card: #000000;
    --banner: #333333;
    --banner-text: #e6e6e6;
    --text: #ffffff;
    --art-navy: #27336a;
    --art-steel: #b9bec6;
  }
  * { margin: 0; padding: 0; box-sizing: border-box; }
  html, body { width: 1200px; height: 900px; overflow: hidden; }
  body {
    background: var(--backdrop);
    position: relative;
    font-family: "Open Sans", sans-serif;
  }
  .business-card {
    position: absolute;
    left: 100px;
    top: 164px;
    width: 1000px;
    height: 572px;
    background: var(--card);
    color: var(--text);
    box-shadow: 0 20px 50px rgba(0,0,0,0.55);
  }
  .company-banner {
    position: absolute;
    left: 36px;
    top: 36px;
    width: 928px;
    height: 62px;
    background: var(--banner);
    border-radius: 10px;
    display: flex;
    align-items: center;
    padding-left: 40px;
  }
  .company-name {
    font-family: "Cinzel", serif;
    font-weight: 400;
    font-size: 34px;
    letter-spacing: 2px;
    color: var(--banner-text);
    white-space: nowrap;
  }
  .contact-name {
    position: absolute;
    left: 120px;
    top: 140px;
    font-size: 40px;
    font-weight: 400;
    letter-spacing: 0.5px;
  }
  .contact-phone {
    position: absolute;
    left: 132px;
    top: 204px;
    display: flex;
    align-items: center;
    gap: 38px;
    font-size: 24px;
  }
  .contact-phone svg { width: 20px; height: 20px; fill: var(--text); }
  .services-title {
    position: absolute;
    left: 196px;
    top: 292px;
    font-size: 32px;
  }
  .services-list {
    position: absolute;
    left: 296px;
    top: 346px;
    list-style: none;
    font-size: 24px;
    line-height: 38px;
  }
  .services-list li { position: relative; padding-left: 34px; }
  .services-list li::before {
    content: "";
    position: absolute;
    left: 0;
    top: 14px;
    width: 11px;
    height: 11px;
    border-radius: 50%;
    background: var(--text);
  }
  .service-art {
    position: absolute;
    left: 580px;
    top: 128px;
    width: 370px;
    height: 200px;
    border-radius: 40px;
    background: radial-gradient(ellipse at 40% 60%, var(--art-navy) 0%, #1a2247 55%, var(--card) 100%),
                linear-gradient(90deg, var(--art-navy), var(--art-steel));
  }
</style>
</head>
<body>
  <article class="business-card">
    <div class="company-banner">
      <h1 class="company-name">Brightpath Automotive &amp; Diesel Repair</h1>
    </div>

    <p class="contact-name">Dean Marlowe</p>
    <p class="contact-phone">
      <svg viewBox="0 0 24 24" aria-hidden="true"><path d="M6.6 10.8a15.1 15.1 0 0 0 6.6 6.6l2.2-2.2a1 1 0 0 1 1-.25 11.4 11.4 0 0 0 3.6.57 1 1 0 0 1 1 1V20a1 1 0 0 1-1 1A17 17 0 0 1 3 4a1 1 0 0 1 1-1h3.5a1 1 0 0 1 1 1c0 1.25.2 2.45.57 3.57a1 1 0 0 1-.25 1z"/></svg>
      <span>534 861 2093</span>
    </p>

    <h2 class="services-title">Services</h2>
    <ul class="services-list">
      <li>Roadside assistance</li>
      <li>Fleet maintenance</li>
      <li>Diesel repairs</li>
      <li>Mobile repairs</li>
    </ul>

    <div class="service-art" role="img" aria-label="Illustration of a blue convertible car with a crossed wrench and yellow-handled screwdriver"></div>
  </article>
</body>
</html>
```